Modern business card design for professional copywriter

I'd like a business card design that I can use to have my cards printed out by quillprint.com as a squared corners business card (see artwork and design guidelines here: https://help.quillprint.com/hc/en-gb/sections/200570950-QUILL-Product-Templates)

The design should be clean and modern and reflect the colours, tone and branding on my website: https://tessavorrin.com.au

Target Market(s)

Professionals, B2B small business owners

Industry/Entity Type

Business

Contact Information for Business Card

Tessa Vorrin
m: 0468 905 327
e: tessa@tessavorrin.com.au
w: tessavorrin.com.au

Font styles to use
Sans Serif

Requirements
Must have
• Tagline: "Bright copywriting for busy business owners"
• Brand colours: fd8000, 009984, 666666 and black
Nice to have

```html
<!DOCTYPE html>
<html lang="en">
<head>
<meta charset="utf-8">
<title>Tessa Vorrin – Business Card</title>
<link href="https://fonts.googleapis.com/css2?family=Open+Sans:wght@400;600;700&display=swap" rel="stylesheet">
<style>
  :root {
    --orange: #fd8000;
    --teal: #009984;
    --grey: #666666;
    --silver: #d4d4d4;
    --card: #0d0d0d;
    --backdrop: #4a423c;
    --white: #f2f2f2;
  }
  * { box-sizing: border-box; margin: 0; padding: 0; }
  html, body {
    width: 1200px; height: 900px; overflow: hidden;
    background: var(--backdrop);
    font-family: "Open Sans", Arial, sans-serif;
  }
  .stage {
    position: relative; width: 1200px; height: 900px;
    display: flex; align-items: center; justify-content: center; gap: 50px;
  }
  .card {
    position: relative; width: 525px; height: 340px;
    background: var(--card);
    box-shadow: 0 10px 30px rgba(0,0,0,.45);
  }

  /* Front */
  .brand {
    position: absolute; left: 40px; top: 150px;
    display: flex; align-items: center; gap: 10px;
  }
  .brand-mark { width: 14px; height: 14px; background: var(--orange); }
  .brand-name {
    font-size: 30px; font-weight: 600; color: var(--teal); letter-spacing: .2px;
    white-space: nowrap;
  }
  .divider {
    position: absolute; left: 290px; top: 38px; width: 1px; height: 150px;
    background: linear-gradient(var(--orange), rgba(253,128,0,.15));
  }
  .contact { position: absolute; left: 315px; top: 46px; }
  .person {
    font-size: 19px; font-weight: 600; letter-spacing: .5px; text-transform: uppercase;
    margin-bottom: 30px; white-space: nowrap;
  }
  .person .first { color: var(--teal); }
  .person .last { color: var(--orange); }
  .contact-list { list-style: none; }
  .contact-list li {
    display: flex; align-items: center; gap: 9px;
    font-size: 13.5px; color: var(--white); line-height: 20px; white-space: nowrap;
  }
  .contact-list svg { width: 11px; height: 11px; flex: none; fill: var(--teal); }
  .tagline {
    position: absolute; left: 40px; bottom: 30px;
    font-size: 17.5px; font-weight: 700; color: var(--teal);
    text-transform: uppercase; letter-spacing: .2px; white-space: nowrap;
  }

  /* Back */
  .card-back { display: flex; align-items: center; justify-content: center; }
  .card-back .brand { position: static; }
  .card-back .brand-mark { width: 18px; height: 18px; background: var(--silver); }
  .card-back .brand-name { font-size: 40px; color: var(--silver); }
</style>
</head>
<body>
<main class="stage">
  <section class="card card-front" aria-label="Business card front">
    <div class="brand">
      <span class="brand-mark"></span>
      <span class="brand-name">Tessa Vorrin</span>
    </div>
    <div class="divider"></div>
    <div class="contact">
      <p class="person"><span class="first">Tessa</span> <span class="last">Vorrin</span></p>
      <ul class="contact-list">
        <li>
          <svg viewBox="0 0 12 12" aria-hidden="true"><path d="M3 0h6a1 1 0 0 1 1 1v10a1 1 0 0 1-1 1H3a1 1 0 0 1-1-1V1a1 1 0 0 1 1-1zm0 1.5V9.5h6V1.5zM6 10a.6.6 0 1 0 0 1.2A.6.6 0 0 0 6 10z"/></svg>
          0468 905 327
        </li>
        <li>
          <svg viewBox="0 0 12 12" aria-hidden="true"><path d="M0 2h12v1L6 7 0 3zM0 4.2l6 4 6-4V10H0z"/></svg>
          tessa@tessavorrin.com.au
        </li>
        <li>
          <svg viewBox="0 0 12 12" aria-hidden="true"><circle cx="6" cy="6" r="6"/><path d="M1 6h10M6 1c2 2.5 2 7.5 0 10M6 1c-2 2.5-2 7.5 0 10" stroke="#0d0d0d" stroke-width="1" fill="none"/></svg>
          tessavorrin.com.au
        </li>
      </ul>
    </div>
    <p class="tagline">Bright copywriting for busy business owners</p>
  </section>

  <section class="card card-back" aria-label="Business card back">
    <div class="brand">
      <span class="brand-mark"></span>
      <span class="brand-name">Tessa Vorrin</span>
    </div>
  </section>
</main>
</body>
</html>
```